Up to the Challenge - PPT Template with Splash Slide

We are looking for a PPT template that has 4 slides.
1. Splash slide (Creative, fun, no content, a visual representation of the theme)
2. Section header slide
3. Content Slide
4. Content Slide, another design option
The theme is 'UP to the Challenge'. The design should reflect this theme.
The colors should be in Purple (#864B99), Blue (#0A80C2), and Green (#52B054).

```html
<!DOCTYPE html>
<html lang="en">
<head>
<meta charset="utf-8">
<title>Up to the Challenge – Slide Template</title>
<link href="https://fonts.googleapis.com/css2?family=Lato:wght@400;700&family=Ubuntu:wght@500;700&display=swap" rel="stylesheet">
<style>
  :root {
    --canvas: #c4dae9;
    --purple: #864b99;
    --blue: #0a80c2;
    --green: #52b054;
    --ink: #2b2b2b;
    --white: #ffffff;
    --mist-top: #eef4f9;
    --mist-mid: #dfe8f0;
    --mist-low: #f3f6f9;
  }
  * { box-sizing: border-box; margin: 0; padding: 0; }
  html, body { width: 1055px; height: 1200px; overflow: hidden; }
  body {
    background: var(--canvas);
    font-family: "Lato", sans-serif;
    color: var(--ink);
    position: relative;
  }
  .slide {
    position: absolute;
    width: 496px;
    height: 278px;
    overflow: hidden;
  }
  .col-a { left: 26px; }
  .col-b { left: 532px; }
  .row-1 { top: 28px; }
  .row-2 { top: 316px; }
  .row-3 { top: 604px; }
  .row-4 { top: 894px; }

  .misty {
    background:
      radial-gradient(ellipse 40% 35% at 52% 38%, #d3dde7 0%, rgba(211,221,231,0) 100%),
      linear-gradient(180deg, var(--mist-top) 0%, var(--mist-mid) 55%, var(--mist-low) 100%);
  }
  .plain { background: var(--white); border-top: 1.5px solid var(--green); }

  .slide-title {
    position: absolute;
    font-family: "Ubuntu", sans-serif;
    font-weight: 700;
    font-size: 15.5px;
    color: var(--purple);
    white-space: nowrap;
  }
  .tab {
    position: absolute;
    left: 0; top: 0;
    width: 201px; height: 27px;
    background: var(--green);
    clip-path: polygon(0 0, 100% 0, 88.5% 100%, 0 100%);
  }
  .tab .slide-title { color: var(--white); left: 32px; top: 4px; }

  .footer {
    position: absolute;
    left: 0; bottom: 0;
    width: 100%; height: 16px;
    background: var(--green);
    color: var(--white);
    font-size: 6.5px;
    text-align: center;
    line-height: 16px;
  }

  .intro {
    position: absolute;
    left: 19px; top: 84px;
    width: 185px;
    font-size: 7.4px;
    line-height: 11.8px;
  }
  .presenter {
    position: absolute;
    left: 19px; top: 148px;
    font-family: "Ubuntu", sans-serif;
    font-weight: 700;
    font-size: 9px;
  }
  .presenter .first { color: var(--purple); }
  .presenter .last { color: #111; }
  .date { position: absolute; left: 19px; top: 203px; font-size: 7.6px; }

  .on-dark .slide-title, .on-dark .intro, .on-dark .presenter span, .on-dark .date { color: var(--white); }
  .on-dark .slide-title, .on-dark .intro, .on-dark .presenter, .on-dark .date { left: 31px; }

  .summit-art {
    position: absolute;
    left: 0; top: 20px;
    width: 470px; height: 258px;
    background:
      radial-gradient(ellipse 42% 70% at 65% 100%, rgba(42,96,150,0.95) 0%, rgba(58,112,165,0.7) 45%, rgba(200,215,230,0) 100%),
      radial-gradient(ellipse 22% 40% at 28% 100%, rgba(42,96,150,0.8) 0%, rgba(200,215,230,0) 100%);
  }
  .sunset-photo {
    position: absolute; inset: 0;
    background:
      radial-gradient(circle at 46% 68%, #fff0c8 0%, rgba(255,240,200,0) 25%),
      linear-gradient(180deg, #d98a3a 0%, #e9a548 45%, #dca255 70%, #4a4644 100%);
  }

  .bullets {
    position: absolute;
    list-style: none;
    font-size: 6.5px;
    line-height: 10.1px;
  }
  .bullets li { margin-bottom: 13.4px; }
  .bullets li::before {
    content: "›";
    display: inline-block;
    width: 6px; height: 6px;
    margin-right: 2px;
    border-radius: 50%;
    background: var(--purple);
    color: var(--white);
    font-size: 6px;
    line-height: 5.5px;
    text-align: center;
    font-weight: 700;
    vertical-align: -0.5px;
  }
  .bullets.left-col { left: 19px; top: 50px; width: 192px; }
  .bullets.right-col { left: 234px; top: 50px; width: 192px; }

  .body-copy {
    position: absolute;
    left: 32px; top: 59px;
    width: 412px;
    font-size: 8.8px;
    line-height: 13.7px;
    color: #333;
  }
  .body-copy p + p { margin-top: 6px; }

  .lead {
    position: absolute;
    left: 19px; top: 56px;
    width: 212px;
    font-size: 7px;
    line-height: 11.7px;
  }
  .bullets.stacked { left: 19px; top: 115px; width: 200px; }
  .bullets.stacked li { margin-bottom: 6.5px; }

  .peak-photo {
    position: absolute;
    left: 270px; top: 54px;
    width: 182px; height: 181px;
    border-radius: 5px;
    background: linear-gradient(180deg, #e9ecd2 0%, #a9b9a0 45%, #5f7b6c 75%, #34493f 100%);
  }

  .trophy-photo {
    position: absolute;
    left: 230px; top: 52px;
    width: 228px; height: 184px;
    background:
      radial-gradient(circle at 62% 72%, #ffe08a 0%, rgba(255,224,138,0) 22%),
      linear-gradient(180deg, #9c97a4 0%, #d49a6e 45%, #e07e3a 70%, #3a2c28 100%);
  }
  .text-card {
    position: absolute;
    left: 18px; top: 51px;
    width: 289px; height: 173px;
    background: var(--white);
    box-shadow: 0 0 4px rgba(0,0,0,0.18);
    padding: 13px 14px;
    font-size: 6.1px;
    line-height: 11.6px;
    color: #444;
  }
  .text-card p + p { margin-top: 4px; }
</style>
</head>
<body>

  <!-- Title slide, light -->
  <section class="slide col-a row-1 misty">
    <div class="summit-art" role="img" aria-label="Illustration of a businessman planting a flag on a blue mountain summit among misty peaks"></div>
    <h1 class="slide-title" style="left:19px;top:56px;">Presentation Title Gose Here</h1>
    <p class="intro">Lorem ipsum dolor sit amet, consectetur adipiscing elit, sed do eiusmod tempor incididunt ut labore et dolore magna aliqua.</p>
    <p class="presenter"><span class="first">Mara</span> <span class="last">Quinn</span></p>
    <p class="date">June,06</p>
  </section>

  <!-- Title slide, sunset -->
  <section class="slide col-b row-1 on-dark">
    <div class="sunset-photo" role="img" aria-label="Businessman pushing a large boulder up a slope at sunset"></div>
    <h1 class="slide-title" style="top:56px;">Presentation Title Gose Here</h1>
    <p class="intro">Lorem ipsum dolor sit amet, consectetur adipiscing elit, sed do eiusmod tempor incididunt ut labore et dolore magna aliqua.</p>
    <p class="presenter"><span>Mara Quinn</span></p>
    <p class="date">June,06</p>
    <div class="footer">© 2024 | All rights reserved</div>
  </section>

  <!-- Section slide, light -->
  <section class="slide col-a row-2 misty" role="img" aria-label="Misty snow-capped mountain above clouds">
    <h2 class="slide-title" style="left:19px;top:21px;">Section Slide</h2>
  </section>

  <!-- Section slide, white -->
  <section class="slide col-b row-2 plain">
    <div class="tab"><h2 class="slide-title">Section Slide</h2></div>
    <div class="footer">© 2024 | All rights reserved</div>
  </section>

  <!-- Content slide, two columns -->
  <section class="slide col-a row-3 misty" role="img" aria-label="Misty mountain peaks and clouds">
    <h2 class="slide-title" style="left:19px;top:21px;">Content Slide</h2>
    <ul class="bullets left-col">
      <li>Lorem ipsum dolor sit amet, consectetur adipiscing elit, sed do eiusmod tempor incididunt ut labore et dolore magna aliqua. Quis ipsum suspendisse ultrices gravida.</li>
      <li>Lorem ipsum dolor sit amet, consectetur adipiscing elit, sed do eiusmod tempor incididunt ut labore et dolore magna aliqua. Quis ipsum suspendisse ultrices gravida.</li>
      <li>Lorem ipsum dolor sit amet, consectetur adipiscing elit, sed do eiusmod tempor incididunt ut labore et dolore magna aliqua. Quis ipsum suspendisse ultrices gravida.</li>
      <li>Lorem ipsum dolor sit amet, consectetur adipiscing elit, sed do eiusmod tempor incididunt ut labore et dolore magna aliqua. Quis ipsum suspendisse ultrices gravida.</li>
      <li>Lorem ipsum dolor sit amet, consectetur adipiscing elit, sed do eiusmod tempor incididunt ut labore et dolore magna aliqua. Quis ipsum suspendisse ultrices gravida.</li>
    </ul>
    <ul class="bullets right-col">
      <li>Lorem ipsum dolor sit amet, consectetur adipiscing elit, sed do eiusmod tempor incididunt ut labore et dolore magna aliqua. Quis ipsum suspendisse ultrices gravida.</li>
      <li>Lorem ipsum dolor sit amet, consectetur adipiscing elit, sed do eiusmod tempor incididunt ut labore et dolore magna aliqua. Quis ipsum suspendisse ultrices gravida.</li>
      <li>Lorem ipsum dolor sit amet, consectetur adipiscing elit, sed do eiusmod tempor incididunt ut labore et dolore magna aliqua. Quis ipsum suspendisse ultrices gravida.</li>
      <li>Lorem ipsum dolor sit amet, consectetur adipiscing elit, sed do eiusmod tempor incididunt ut labore et dolore magna aliqua. Quis ipsum suspendisse ultrices gravida.</li>
      <li>Lorem ipsum dolor sit amet, consectetur adipiscing elit, sed do eiusmod tempor incididunt ut labore et dolore magna aliqua. Quis ipsum suspendisse ultrices gravida.</li>
    </ul>
  </section>

  <!-- Content slide, paragraph -->
  <section class="slide col-b row-3 plain">
    <div class="tab"><h2 class="slide-title">Content Slide</h2></div>
    <div class="body-copy">
      <p>Lorem ipsum dolor sit amet, consectetur adipiscing elit, sed do eiusmod tempor incididunt ut labore et dolore magna aliqua. Quis ipsum suspendisse ultrices gravida. Risus commodo viverra maecenas accumsan lacus vel facilisis.</p>
      <p>Lorem ipsum dolor sit amet, consectetur adipiscing elit, sed do eiusmod tempor incididunt ut labore et dolore magna aliqua. Ut enim ad minim veniam, quis nostrud exercitation ullamco laboris nisi ut aliquip ex ea commodo consequat. Duis aute irure dolor in reprehenderit in voluptate velit esse cillum dolore eu fugiat nulla pariatur. Sed ut perspiciatis unde omnis iste natus error sit voluptatem accusantium doloremque laudantium, totam rem aperiam, eaque ipsa quae ab illo inventore veritatis et quasi architecto beatae vitae dicta sunt explicabo. Nemo enim ipsam voluptatem quia voluptas sit aspernatur aut odit aut fugit, sed quia consequuntur magni dolores eos qui ratione voluptatem sequi nesciunt. Neque porro quisquam est, qui dolorem ipsum quia dolor sit amet, consectetur, adipisci velit, sed quia non numquam eius modi tempora incidunt ut labore et dolore magnam aliquam quaerat voluptatem.</p>
    </div>
    <div class="footer">© 2024 | All rights reserved</div>
  </section>

  <!-- Content slide, text and photo -->
  <section class="slide col-a row-4 misty" role="img" aria-label="Misty mountain peaks and clouds">
    <h2 class="slide-title" style="left:22px;top:21px;">Content Slide</h2>
    <p class="lead">Lorem ipsum dolor sit amet, consectetur adipiscing elit, sed do eiusmod tempor incididunt ut labore et dolore magna aliqua. Quis ipsum suspendisse ultrices gravida. Risus commodo viverra maecenas accumsan lacus vel facilisis.</p>
    <ul class="bullets stacked">
      <li>Lorem ipsum dolor sit amet, consectetur adipiscing elit, sed do eiusmod tempor incididunt ut labore et dolore magna aliqua. Quis ipsum suspendisse ultrices gravida.</li>
      <li>Lorem ipsum dolor sit amet, consectetur adipiscing elit, sed do eiusmod tempor incididunt ut labore et dolore magna aliqua. Quis ipsum suspendisse ultrices gravida.</li>
      <li>Lorem ipsum dolor sit amet, consectetur adipiscing elit, sed do eiusmod tempor incididunt ut labore et dolore magna aliqua. Quis ipsum suspendisse ultrices gravida.</li>
    </ul>
    <div class="peak-photo" role="img" aria-label="Hiker with raised arms on a misty mountain summit"></div>
  </section>

  <!-- Content slide, card over photo -->
  <section class="slide col-b row-4 plain">
    <div class="tab"><h2 class="slide-title">Content Slide</h2></div>
    <div class="trophy-photo" role="img" aria-label="Silhouette leaping with a trophy on a rock at sunset"></div>
    <div class="text-card">
      <p>Lorem ipsum dolor sit amet, consectetur adipiscing elit, sed do eiusmod tempor incididunt ut labore et dolore magna aliqua. Ut enim ad minim veniam, quis nostrud exercitation ullamco laboris nisi ut aliquip ex ea commodo consequat. Duis aute irure dolor in reprehenderit in voluptate velit esse cillum dolore eu fugiat nulla pariatur. Sed ut perspiciatis unde omnis iste natus error sit voluptatem accusantium doloremque laudantium, totam rem aperiam, eaque ipsa quae ab illo inventore veritatis et quasi architecto beatae vitae dicta sunt explicabo. Nemo enim ipsam voluptatem quia voluptas sit aspernatur aut odit aut fugit, sed quia consequuntur magni dolores eos qui ratione voluptatem sequi nesciunt.voluptatem.</p>
      <p>Neque porro quisquam est, qui dolorem ipsum quia dolor sit amet, consectetur, adipisci velit, sed quia non numquam eius modi tempora incidunt ut labore et dolore magnam aliquam quaerat voluptatem.</p>
    </div>
    <div class="footer">© 2024 | All rights reserved</div>
  </section>

</body>
</html>
```